High-end construction company needs a business card design

We need a modern looking business card that draws people in, is memorable and looks so good people will want to sick it on their fridges.
On the first side what is needed are:
Logo
My name - Tomasz Brelwik
Title - Managing Director
Website - www.varkelt.co.uk
Email - tomasz@varkelt.co.uk
Telephone - 020 5194 6281
Mobile - 07845139072
On the back side was is needed is a list of all the services we provide:
-Kitchen Renovations
-Bathroom Renovations
-House Renovations
-Garage Conversions
-Extensions
-Loft Conversions
-Conservatories
-Carpentry
-Tiling
-Electrical
-Plumbing & Heating
-Bricklaying
-Landscaping
-Decorating
-Plastering
We would like the colours to be the same shades as on the logo with grey or black for the words.
Target Market(s)
Anyone who needs building work done
Contact Information for Business Card
This business card is for a construction company which strives to deliver excellent service and quality.
The look and feel of the card should represent this.
Requirements
Must have
- On the first side what is needed are:
Logo
My name - Tomasz Brelwik
Title - Managing Director
Website - www.varkelt.co.uk
Email - tomasz@varkelt.co.uk
Telephone - 020 5194 6281
Mobile - 07845139072
Nice to have
- Cool looking features

```html
<!DOCTYPE html>
<html lang="en">
<head>
<meta charset="utf-8">
<title>Varkelt Construction Ltd – Business Card</title>
<link rel="stylesheet" href="https://fonts.googleapis.com/css2?family=Montserrat:wght@400;500;600;800&display=swap">
<style>
  :root {
    --bg: #1e1f20;
    --card-dark: #2f3032;
    --card-light: #f7f7f5;
    --green: #6cc04a;
    --green-deep: #3f8f3a;
    --text-light: #f2f2f2;
    --text-grey: #555a5e;
  }
  * { box-sizing: border-box; margin: 0; padding: 0; }
  html, body { width: 1200px; height: 896px; overflow: hidden; }
  body {
    background: var(--bg);
    font-family: "Montserrat", Arial, sans-serif;
    display: flex;
    flex-direction: column;
    align-items: center;
    justify-content: center;
    gap: 40px;
  }
  .card {
    position: relative;
    width: 700px;
    height: 400px;
    overflow: hidden;
    box-shadow: 0 10px 30px rgba(0,0,0,.5);
  }
  .card::after {
    content: "";
    position: absolute;
    left: 0; right: 0; bottom: 0;
    height: 14px;
    background: linear-gradient(to bottom, var(--green) 0 50%, var(--green-deep) 50% 100%);
  }
  .brand {
    display: flex;
    align-items: center;
    gap: 12px;
    color: var(--green);
    font-weight: 800;
    line-height: 1.05;
  }
  .brand-mark {
    width: 22px; height: 22px;
    background: var(--green);
    flex: none;
  }
  .brand-name { font-size: 46px; letter-spacing: 2px; }
  .brand-sub { font-size: 17px; letter-spacing: 3px; display: block; }

  /* back: services */
  .card-services {
    background: var(--card-dark);
    display: flex;
    flex-direction: column;
    align-items: center;
    padding-top: 52px;
  }
  .services-head {
    display: flex;
    align-items: center;
    gap: 16px;
    margin: 34px 0 22px;
    width: 560px;
  }
  .services-head .rule { flex: 1; height: 2px; background: var(--green); }
  .services-title { color: var(--green); font-weight: 800; font-size: 22px; letter-spacing: 1px; }
  .services-list { list-style: none; text-align: center; color: var(--text-light); font-size: 17px; line-height: 1.6; font-weight: 500; }
  .services-list .dot { color: var(--green); margin: 0 6px; }

  /* front: contact */
  .card-contact {
    background: var(--card-light);
    display: flex;
    align-items: center;
    padding: 0 50px 14px 56px;
  }
  .card-contact .brand-name { font-size: 40px; }
  .card-contact .brand-sub { font-size: 15px; }
  .divider { width: 2px; height: 250px; background: var(--green); margin: 0 40px; }
  .person-name { color: var(--green); font-weight: 800; font-size: 30px; text-transform: uppercase; letter-spacing: .5px; }
  .person-title { color: var(--text-grey); font-size: 18px; margin-top: 2px; }
  .contact-list { list-style: none; margin-top: 26px; color: var(--text-grey); font-size: 19px; line-height: 1.65; }
  .contact-list li { display: flex; align-items: center; gap: 10px; }
  .contact-list svg { width: 16px; height: 16px; fill: var(--green-deep); flex: none; }
</style>
</head>
<body>

<section class="card card-services">
  <div class="brand">
    <span class="brand-mark"></span>
    <div><span class="brand-name">VARKELT</span><span class="brand-sub">CONSTRUCTION LTD</span></div>
  </div>
  <div class="services-head">
    <span class="rule"></span><span class="services-title">SERVICES</span><span class="rule"></span>
  </div>
  <ul class="services-list">
    <li><span class="dot">•</span>Kitchen Renovations<span class="dot">•</span>Bathroom Renovations<span class="dot">•</span>House Renovations</li>
    <li><span class="dot">•</span>Garage Conversions<span class="dot">•</span>Extensions<span class="dot">•</span>Loft Conversions<span class="dot">•</span>Conservatories</li>
    <li><span class="dot">•</span>Carpentry<span class="dot">•</span>Tiling<span class="dot">•</span>Electrical<span class="dot">•</span>Plumbing &amp; Heating</li>
    <li><span class="dot">•</span>Bricklaying<span class="dot">•</span>Landscaping<span class="dot">•</span>Decorating<span class="dot">•</span>Plastering</li>
  </ul>
</section>

<section class="card card-contact">
  <div class="brand">
    <span class="brand-mark"></span>
    <div><span class="brand-name">VARKELT</span><span class="brand-sub">CONSTRUCTION LTD</span></div>
  </div>
  <span class="divider"></span>
  <div class="person">
    <h1 class="person-name">Tomasz Brelwik</h1>
    <p class="person-title">Managing Director</p>
    <ul class="contact-list">
      <li><svg viewBox="0 0 24 24"><path d="M6.6 10.8a15 15 0 0 0 6.6 6.6l2.2-2.2c.3-.3.7-.4 1-.2 1.1.4 2.3.6 3.6.6.6 0 1 .4 1 1V20c0 .6-.4 1-1 1A17 17 0 0 1 3 4c0-.6.4-1 1-1h3.5c.6 0 1 .4 1 1 0 1.3.2 2.5.6 3.6.1.3 0 .7-.2 1z"/></svg>020 5194 6281</li>
      <li><svg viewBox="0 0 24 24"><path d="M7 1h10a2 2 0 0 1 2 2v18a2 2 0 0 1-2 2H7a2 2 0 0 1-2-2V3a2 2 0 0 1 2-2zm0 3v14h10V4zm5 15.5a1 1 0 1 0 0 2 1 1 0 0 0 0-2z"/></svg>07845139072</li>
      <li><svg viewBox="0 0 24 24"><path d="M2 5h20v14H2zm2 2v.5l8 5 8-5V7zm0 2.8V17h16V9.8l-8 5z"/></svg>tomasz@varkelt.co.uk</li>
      <li><svg viewBox="0 0 24 24"><path d="M12 2a10 10 0 1 0 0 20 10 10 0 0 0 0-20zm6.9 9h-3a15 15 0 0 0-1.3-5.9A8 8 0 0 1 18.9 11zM12 4c.9 1.2 1.8 3.7 1.9 7h-3.8c.1-3.3 1-5.8 1.9-7zM9.4 5.1A15 15 0 0 0 8.1 11h-3a8 8 0 0 1 4.3-5.9zM5.1 13h3a15 15 0 0 0 1.3 5.9A8 8 0 0 1 5.1 13zM12 20c-.9-1.2-1.8-3.7-1.9-7h3.8c-.1 3.3-1 5.8-1.9 7zm2.6-1.1a15 15 0 0 0 1.3-5.9h3a8 8 0 0 1-4.3 5.9z"/></svg>www.varkelt.co.uk</li>
    </ul>
  </div>
</section>

</body>
</html>
```